Business Card Design For Marketing Agnecy LVP

Need business card design for marketing agency.

Doug Fenwick
President, CEO
1-555-302-4196
doug@boldpromoperksgroup.example
www.BoldPromoPerksGroup.example

Back Side:
Boost Sales Using Rewards, Incentives & Giveaways
Get A Free Sample Package

Target Market(s)

B2B

Industry/Entity Type

Marketing

Contact Information for Business Card

Doug Fenwick
President, CEO
1-555-302-4196

Back Side:
Get A Free Sample Package

Please note that my current url is OLD DESIGN. I am working on new design and want the business card to match color themes at least on new site. Here is the demo link for new site so you can see the colors I use, etc.

http://layoutcratehub.example/kq/doug/lvp_final/index.html

Requirements
Must have
• Please note that my current url is OLD DESIGN. I am working on new design and want the business card to match color themes at least on new site. Here is the demo link for new site so you can see the colors I use, etc.

Nice to have

Should not have

```html
<!DOCTYPE html>
<html lang="en">
<head>
<meta charset="utf-8">
<title>LVP Business Card – Front and Back</title>
<link rel="stylesheet" href="https://fonts.googleapis.com/css2?family=Arimo:wght@400;700&display=swap">
<style>
  :root {
    --brand-blue: #1f78c1;
    --ink-gray: #4d4f53;
    --rule-gray: #55575b;
    --card-white: #ffffff;
    --stage: #e9ebee;
  }
  * { box-sizing: border-box; margin: 0; padding: 0; }
  html, body {
    width: 1200px; height: 900px; overflow: hidden;
    background: var(--stage);
    font-family: "Arimo", Arial, sans-serif;
  }
  .card {
    position: absolute;
    width: 520px; height: 297px;
    border-radius: 4px;
    box-shadow: 0 6px 18px rgba(0,0,0,.18);
    overflow: hidden;
  }
  /* Back side */
  .card-back {
    left: 70px; top: 170px;
    background: var(--brand-blue);
    color: var(--card-white);
    text-align: center;
  }
  .card-back .brand-name {
    margin-top: 62px;
    font-size: 84px; font-weight: 700;
    letter-spacing: 2px; line-height: 1;
  }
  .card-back .tagline {
    margin-top: 46px;
    font-size: 16px; line-height: 1.3;
  }
  .card-back .tagline .dot {
    display: inline-block; width: 6px; height: 6px;
    border-radius: 50%; background: var(--card-white);
    vertical-align: middle; margin: 0 8px;
  }
  /* Front side */
  .card-front {
    left: 610px; top: 430px;
    background: var(--card-white);
  }
  .footer-rule {
    position: absolute; left: 0; right: 0; bottom: 46px;
    height: 4px; background: var(--rule-gray);
  }
  .footer-band {
    position: absolute; left: 0; right: 0; bottom: 0;
    height: 40px; background: var(--brand-blue);
  }
  .holder { position: absolute; left: 34px; top: 40px; }
  .holder-name {
    color: var(--brand-blue);
    font-size: 20px; font-weight: 700; text-transform: uppercase;
  }
  .holder-title { color: var(--ink-gray); font-size: 15px; margin-top: 2px; }
  .card-front .brand-name {
    position: absolute; right: 40px; top: 36px;
    color: var(--brand-blue);
    font-size: 58px; font-weight: 700; letter-spacing: 1px; line-height: 1;
  }
  .contact-list {
    position: absolute; left: 34px; top: 166px;
    list-style: none; color: var(--ink-gray); font-size: 14.5px;
  }
  .contact-list li { display: flex; align-items: center; gap: 7px; height: 22px; }
  .contact-list svg { width: 13px; height: 13px; fill: var(--brand-blue); flex: none; }
  .contact-list .highlight { color: var(--brand-blue); }
</style>
</head>
<body>

<section class="card card-back" aria-label="Business card back">
  <div class="brand-name">LVP</div>
  <p class="tagline">
    Boost Sales Using Rewards<span class="dot"></span>Incentives &amp; Giveaways<br>
    Get A Free Sample Package
  </p>
</section>

<section class="card card-front" aria-label="Business card front">
  <div class="footer-rule" aria-hidden="true"></div>
  <div class="footer-band" aria-hidden="true"></div>

  <div class="holder">
    <h1 class="holder-name">Doug Fenwick</h1>
    <p class="holder-title">President, CEO</p>
  </div>

  <div class="brand-name">LVP</div>

  <ul class="contact-list">
    <li>
      <svg viewBox="0 0 16 16"><path d="M3 1h3l1.5 4-2 1.3a9 9 0 0 0 4.2 4.2L11 8.5l4 1.5v3a2 2 0 0 1-2 2A12 12 0 0 1 1 3a2 2 0 0 1 2-2z"/></svg>
      1-555-302-4196
    </li>
    <li>
      <svg viewBox="0 0 16 16"><path d="M1 3h14v10H1z M1.5 3.5 8 9l6.5-5.5" stroke="#fff" stroke-width="1.2"/></svg>
      doug@boldpromoperksgroup.example
    </li>
    <li>
      <svg viewBox="0 0 16 16"><circle cx="8" cy="8" r="7"/><path d="M1 8h14M8 1c-3 3-3 11 0 14M8 1c3 3 3 11 0 14" stroke="#fff" fill="none" stroke-width="1"/></svg>
      <span>www.<span class="highlight">BoldPromoPerksGroup</span>.example</span>
    </li>
  </ul>
</section>

</body>
</html>
```